Velmora Consulting Business

** Please add the content information from my old business card
1. I would like to see a two sided business card with both options with the 1st Option--Tallow Spire-new WHITE BACKGROUND LOGO
2 nd Option-Tallow Spire - new BLACK- Background Logo
3rd -Option a business card with my Photo on the card
Please add the new word to the card information:
EXECUTION
AS THE OWNER'S REP
WE AIM TO ACHIEVE YOUR
INFRASTRUCTURE VISION with
OUR SPECIALIZATION & EXECUTION in:

FUNDING Planning
BUSINESS Planning
INFRASTRUCTURE Planning
PROJECT Management
Since 2012
_____________________________________________________________________
I want to get spot uv raised printing. I was liking a a nice rich white linen paper stock with black writing & NOT A COLORED CARD other than a variety of white or black cards concept

```html
<!DOCTYPE html>
<html lang="en">
<head>
<meta charset="utf-8">
<title>Velmora Consulting – Business Card</title>
<link href="https://fonts.googleapis.com/css2?family=Montserrat:wght@400;500;600;700&family=Tinos:wght@400;700&display=swap" rel="stylesheet">
<style>
  :root {
    --stage: #1b1b1b;
    --card-white: #ffffff;
    --card-black: #050505;
    --ink: #1a1a1a;
    --red: #e3172e;
    --muted-red: #8c1020;
    --white: #ffffff;
    --faint: #1d1d1d;
  }
  * { margin: 0; padding: 0; box-sizing: border-box; }
  html, body { width: 1200px; height: 1059px; overflow: hidden; background: var(--stage); }
  body { position: relative; font-family: "Montserrat", Arial, sans-serif; }

  .card { position: absolute; border-radius: 22px; overflow: hidden; }
  .card--front { left: 256px; top: 98px; width: 689px; height: 381px; background: var(--card-white); }
  .card--back { left: 253px; top: 545px; width: 708px; height: 394px; background: var(--card-black); }

  .brand { position: absolute; font-weight: 700; line-height: 1.05; font-size: 36px; }
  .card--front .brand { left: 72px; top: 106px; width: 210px; color: var(--ink); }
  .card--back .brand { left: 96px; top: 166px; width: 210px; color: var(--white); }

  .divider { position: absolute; width: 2px; background: var(--red); }
  .card--front .divider { left: 309px; top: 90px; height: 150px; }
  .card--back .divider { left: 337px; top: 105px; height: 210px; width: 1px; background: var(--muted-red); }

  .contact { position: absolute; left: 322px; top: 90px; color: var(--ink); }
  .contact__name { font-size: 21.5px; font-weight: 700; color: var(--red); white-space: nowrap; }
  .contact__title { font-size: 12px; font-weight: 500; margin-top: 2px; letter-spacing: 0.2px; }
  .contact__cities { font-size: 14.5px; font-weight: 500; margin: 18px 0 10px 7px; white-space: nowrap; }
  .contact__list { list-style: none; }
  .contact__item { display: flex; align-items: center; font-size: 14.5px; font-weight: 500; height: 20.5px; }
  .contact__icon { width: 16px; height: 12px; margin: 0 16px 0 5px; fill: var(--red); }

  .wave { position: absolute; left: 0; bottom: 0; width: 689px; height: 381px; }

  .pitch { position: absolute; left: 359px; top: 102px; font-family: "Tinos", "Times New Roman", serif; color: var(--red); font-size: 14.5px; line-height: 19px; }
  .pitch__strong { font-family: "Montserrat", Arial, sans-serif; font-weight: 700; font-size: 14px; }

  .services { position: absolute; left: 362px; top: 201px; list-style: none; }
  .services__item { display: flex; align-items: center; height: 29.5px; color: var(--white); font-size: 15px; font-weight: 500; letter-spacing: 0.3px; }
  .services__bullet { width: 9px; height: 9px; background: var(--red); transform: rotate(45deg); margin: 0 16px 0 6px; }

  .since { position: absolute; left: 538px; top: 354px; color: var(--faint); font-size: 14px; }
</style>
</head>
<body>
  <section class="card card--front">
    <div class="brand">Velmora Consulting</div>
    <div class="divider"></div>
    <div class="contact">
      <div class="contact__name">Marisol Keane-Dorvald</div>
      <div class="contact__title">CEO / LEAD PROJECT MANAGER</div>
      <div class="contact__cities">Cobalt Bay NT · Larkhaven NB</div>
      <ul class="contact__list">
        <li class="contact__item">
          <svg class="contact__icon" viewBox="0 0 16 12"><path d="M1 4 C4 0 12 0 15 4 L13 6 L11 4 L5 4 L3 6 Z M4 6 L12 6 L14 11 L2 11 Z"/></svg>867.555.0182</li>
        <li class="contact__item">
          <svg class="contact__icon" viewBox="0 0 16 12"><path d="M1 1 H15 V11 H1 Z"/><path d="M1 1 L8 7 L15 1" fill="none" stroke="#fff" stroke-width="1.3"/></svg>mari@velmora.ca</li>
        <li class="contact__item">
          <svg class="contact__icon" viewBox="0 0 16 12"><circle cx="8" cy="6" r="5.8"/><path d="M3 4 H13 M3 8 H13 M8 0.5 V11.5" stroke="#fff" stroke-width="0.9" fill="none"/></svg>www.velmora.ca</li>
      </ul>
    </div>
    <svg class="wave" viewBox="0 0 689 381" aria-hidden="true">
      <path d="M0 295 C120 280 280 320 440 352 C560 372 640 352 689 325 L689 381 L0 381 Z" fill="var(--red)"/>
      <path d="M0 298 C120 284 280 325 440 357 C560 378 640 360 689 332 L689 381 L0 381 Z" fill="var(--card-black)"/>
    </svg>
  </section>

  <section class="card card--back">
    <div class="brand">Velmora Consulting</div>
    <div class="divider"></div>
    <p class="pitch">
      AS THE <span class="pitch__strong">OWNER'S REP</span><br>
      WE AIM TO ACHIEVE YOUR<br>
      INFRASTRUCTURE VISION with<br>
      OUR SPECIALIZATION in:
    </p>
    <ul class="services">
      <li class="services__item"><span class="services__bullet"></span>FUNDING Planning</li>
      <li class="services__item"><span class="services__bullet"></span>BUSINESS Planning</li>
      <li class="services__item"><span class="services__bullet"></span>INFRASTRUCTURE Planning</li>
      <li class="services__item"><span class="services__bullet"></span>PROJECT Management</li>
    </ul>
    <div class="since">Since 2012</div>
  </section>
</body>
</html>
```